Letter and Envelope Design For Harborline Realty

Please design a letter and an envelope incorporating our logo (See Attached). We are also launched a business card contest. Since we want them to match, please feel free to submit a design for both the business card and also the letter design and envelope.

Requirements
Must have
• The envelope, the letter and the business cards must match somehow connecting the designs. We want them to have something that holds them together besides the logo.

```html
<!DOCTYPE html>
<html lang="en">
<head>
<meta charset="utf-8">
<title>Harborline Realty — Envelope</title>
<link href="https://fonts.googleapis.com/css2?family=Montserrat:wght@600&family=Lato:wght@400&display=swap" rel="stylesheet">
<style>
  :root{
    --navy:#2b2f7e;
    --paper:#ffffff;
    --ink:#4a4a4f;
    --grey:#55575c;
    --ghost:#ecebf4;
    --stage:#e9e9ec;
  }
  *{margin:0;padding:0;box-sizing:border-box}
  html,body{width:1200px;height:895px;overflow:hidden;background:var(--stage)}
  .canvas{position:relative;width:1200px;height:895px}
  .envelope{position:absolute;left:230px;width:740px;height:370px;background:var(--paper);
    box-shadow:0 2px 8px rgba(0,0,0,.12);overflow:hidden}
  .envelope--back{top:40px}
  .envelope--front{top:480px}
  .flap{position:absolute;inset:0 0 auto 0;width:740px;height:70px}
  .ghost-ring{position:absolute;right:70px;top:-70px;width:250px;height:250px;border-radius:50%;
    border:6px solid var(--ghost)}
  .brand{position:absolute;left:50px;top:46px;display:flex;align-items:center;gap:12px}
  .brand__dot{width:46px;height:46px;border-radius:50%;border:3px solid var(--navy)}
  .brand__name{font-family:"Montserrat",sans-serif;font-weight:600;font-size:20px;letter-spacing:2px;
    color:var(--navy);text-transform:uppercase}
  .contact{position:absolute;font-family:"Lato",sans-serif;font-size:12px;color:var(--ink);line-height:1.55}
  .contact li{list-style:none;display:flex;align-items:center;gap:7px}
  .contact svg{width:10px;height:10px;fill:var(--navy);flex:none}
  .contact--phone{left:110px;bottom:42px}
  .contact--web{left:390px;bottom:42px}
  .contact--address{right:58px;top:198px;text-align:right}
  .tab{position:absolute}
  .tab--navy{right:0;top:246px;width:22px;height:26px;background:var(--navy)}
  .tab--grey{left:0;bottom:30px;width:24px;height:30px;background:var(--grey)}
</style>
</head>
<body>
<main class="canvas">
  <section class="envelope envelope--back" aria-label="Envelope back">
    <svg class="flap" viewBox="0 0 740 70" aria-hidden="true">
      <polygon points="0,0 740,0 715,70 50,70" fill="var(--navy)"/>
      <circle cx="330" cy="35" r="20" fill="none" stroke="#fff" stroke-width="2.5"/>
    </svg>
  </section>

  <section class="envelope envelope--front" aria-label="Envelope front">
    <div class="ghost-ring" aria-hidden="true"></div>
    <div class="brand">
      <span class="brand__dot" aria-hidden="true"></span>
      <span class="brand__name">Harborline Realty</span>
    </div>

    <ul class="contact contact--phone">
      <li><svg viewBox="0 0 10 10"><path d="M2 0h2l1 3-1.5 1a6 6 0 0 0 2.5 2.5L7 5l3 1v2a2 2 0 0 1-2 2A8 8 0 0 1 0 2a2 2 0 0 1 2-2z"/></svg>555-210-4836</li>
      <li><svg viewBox="0 0 10 10"><rect x="2" y="0" width="6" height="3"/><rect x="0" y="3.5" width="10" height="4" rx="1"/><rect x="2" y="7" width="6" height="3"/></svg>555-210-4837</li>
    </ul>

    <ul class="contact contact--web">
      <li><svg viewBox="0 0 10 10"><path d="M0 1.5h10v7H0z M0 1.5l5 4 5-4" /></svg>dlowe@harborline.com</li>
      <li><svg viewBox="0 0 10 10"><circle cx="5" cy="5" r="5"/></svg>www.harborline.com</li>
    </ul>

    <p class="contact contact--address">48 Quayside Row<br>Suite # B, Bristol, UK 40215</p>

    <span class="tab tab--navy" aria-hidden="true"></span>
    <span class="tab tab--grey" aria-hidden="true"></span>
  </section>
</main>
</body>
</html>
```